Mobile digital movie retailer needs design for rewards program app

We would like designs for an 1-page Android app that allows users to rent new release movies and promotes loyalty through a rewards program. The rewards program should have 5-6 tiers -- users earn points for each movie they rent. Users in higher tiers get special offers like free rentals and early access to upcoming titles.
We only offer 5-10 movies at a single time, so there's no need for a sorting or filtering. A simple list will do.
The designs should communicate the following: user's current tier, how close the user is to achieving the next tier, # of movies the user has purchased (and other relevant stats).

```html
<!DOCTYPE html>
<html lang="en">
<head>
<meta charset="utf-8">
<title>App name – Rewards</title>
<link rel="stylesheet" href="https://fonts.googleapis.com/css2?family=Roboto:wght@300;400&display=swap">
<style>
  :root {
    --orange: #ec6b0b;
    --orange-light: #f6a04a;
    --cyan: #35e0f0;
    --panel: #ebe7e6;
    --dial: #f7f5f5;
    --band: #626262;
    --white: #ffffff;
    --ink: #111111;
    --muted: #555555;
    --price: #e00000;
    --list-bg: #f2f2f2;
  }
  * { box-sizing: border-box; margin: 0; padding: 0; }
  html, body { width: 676px; height: 1200px; overflow: hidden; }
  body {
    font-family: "Roboto", "Helvetica Neue", Arial, sans-serif;
    background: var(--list-bg);
    position: relative;
  }
  .app-bar {
    height: 95px;
    background: var(--orange);
    position: relative;
    display: flex;
    align-items: center;
    justify-content: center;
  }
  .menu-icon { position: absolute; left: 26px; top: 28px; }
  .app-title { color: var(--white); font-size: 35px; font-weight: 400; }
  .level-panel {
    height: 346px;
    background: var(--panel);
    display: flex;
    align-items: center;
    justify-content: center;
  }
  .level-dial { position: relative; width: 260px; height: 260px; }
  .level-dial svg { position: absolute; inset: 0; }
  .level-label {
    position: absolute; top: 48px; width: 100%; text-align: center;
    color: var(--orange-light); font-size: 27px; font-weight: 300;
  }
  .level-value {
    position: absolute; top: 76px; width: 100%; text-align: center;
    color: var(--orange); font-size: 104px; font-weight: 300; line-height: 1;
  }
  .stats-band {
    height: 110px;
    background: var(--band);
    display: flex;
    align-items: center;
  }
  .stat {
    flex: 1; text-align: center; color: var(--white);
  }
  .stat + .stat { border-left: 1px solid #bdbdbd; }
  .stat-value { color: var(--orange); font-size: 36px; font-weight: 400; line-height: 1.1; }
  .stat-label { font-size: 29px; font-weight: 300; }
  .movie-list { list-style: none; padding-top: 17px; }
  .movie-card {
    height: 168px;
    background: var(--white);
    margin-bottom: 16px;
    box-shadow: 0 4px 4px rgba(0,0,0,.28);
    position: relative;
  }
  .poster {
    position: absolute; left: 12px; top: 9px; width: 102px; height: 151px;
  }
  .movie-title {
    position: absolute; left: 129px; top: 10px;
    font-size: 35px; font-weight: 300; color: var(--ink);
  }
  .movie-genre {
    position: absolute; left: 133px; top: 52px;
    font-size: 24px; font-weight: 300; color: var(--muted);
  }
  .movie-price {
    position: absolute; right: 42px; bottom: 16px;
    font-size: 36px; font-weight: 300; color: var(--price);
  }
</style>
</head>
<body>
  <header class="app-bar">
    <svg class="menu-icon" width="60" height="42" viewBox="0 0 60 42" aria-hidden="true">
      <rect x="0" y="0" width="60" height="6" rx="3" fill="#fff"/>
      <rect x="0" y="18" width="60" height="6" rx="3" fill="#fff"/>
      <rect x="0" y="36" width="60" height="6" rx="3" fill="#fff"/>
    </svg>
    <h1 class="app-title">App name</h1>
  </header>

  <section class="level-panel">
    <div class="level-dial">
      <svg width="260" height="260" viewBox="0 0 260 260" aria-hidden="true">
        <circle cx="130" cy="130" r="120" fill="none" stroke="var(--cyan)" stroke-width="1.5"/>
        <circle cx="130" cy="130" r="116" fill="var(--dial)"/>
        <circle cx="130" cy="130" r="122" fill="none" stroke="var(--orange)" stroke-width="7"
                stroke-dasharray="508 767" transform="rotate(-90 130 130)"/>
        <circle cx="130" cy="130" r="122" fill="none" stroke="var(--orange-light)" stroke-width="2"
                stroke-dasharray="508 767" transform="rotate(-90 130 130)"/>
      </svg>
      <div class="level-label">level</div>
      <div class="level-value">3</div>
    </div>
  </section>

  <section class="stats-band">
    <div class="stat"><div class="stat-value">10</div><div class="stat-label">movies rented</div></div>
    <div class="stat"><div class="stat-value">5</div><div class="stat-label">movies shared</div></div>
  </section>

  <ul class="movie-list">
    <li class="movie-card">
      <div class="poster" role="img" aria-label="Movie poster: driver and sports car" style="background:linear-gradient(160deg,#1d3b66,#d9782a 60%,#1a2336)"></div>
      <h2 class="movie-title">Full Throttle</h2>
      <p class="movie-genre">Action</p>
      <p class="movie-price">2,99 $</p>
    </li>
    <li class="movie-card">
      <div class="poster" role="img" aria-label="Movie poster: masked hero over city" style="background:linear-gradient(160deg,#1f4d8a,#8a2a3a 55%,#101826)"></div>
      <h2 class="movie-title">The Night Climber 2</h2>
      <p class="movie-genre">Action</p>
      <p class="movie-price">2,99 $</p>
    </li>
    <li class="movie-card">
      <div class="poster" role="img" aria-label="Movie poster: man in suit with crowd" style="background:linear-gradient(180deg,#e8c020 0 22%,#5a6b7a 22%,#2a2a2a)"></div>
      <h2 class="movie-title">The Night Climber 2</h2>
      <p class="movie-genre">Action</p>
      <p class="movie-price">2,99 $</p>
    </li>
    <li class="movie-card">
      <div class="poster" role="img" aria-label="Movie poster: hero with shield" style="background:linear-gradient(180deg,#4a5a6a,#2a3440)"></div>
      <h2 class="movie-title">Iron Sentinel 2</h2>
    </li>
  </ul>
</body>
</html>
```